Corvane Capital Business Cards

These are professional business cards that are for my family office.
Put fake emails and phone numbers as of now until I finalize those components. This family office controls my families investments, assets, and future. The cards should be professional.
..
.
.
.
I just uploaded another variation of a logo I would like to see as a business card to I am inbeteen which logo to use

Target Market(s)

business

Industry/Entity Type

business

Contact Information for Business Card

Professional, wealth related, finance related.

Requirements
Must have
• Logo

```html
<!DOCTYPE html>
<html lang="en">
<head>
<meta charset="utf-8">
<title>Corvane Capital – Business Cards</title>
<link href="https://fonts.googleapis.com/css2?family=Lato:wght@400;700&display=swap" rel="stylesheet">
<style>
  :root {
    --stage: #e9e7e4;
    --navy: #22283a;
    --navy-deep: #1a1f2e;
    --navy-soft: #2b3246;
    --ink: #2a2f3d;
    --paper: #ffffff;
    --muted: #4a4f5c;
    --dot-grey: #b3b3b3;
  }
  * { box-sizing: border-box; margin: 0; padding: 0; }
  html, body {
    width: 1200px; height: 900px; overflow: hidden;
    background: var(--stage);
    font-family: "Lato", sans-serif;
  }
  .stage {
    position: relative; width: 1200px; height: 900px;
  }
  .card {
    position: absolute; left: 250px; width: 700px; height: 400px;
    box-shadow: 0 6px 18px rgba(0,0,0,0.18);
    overflow: hidden;
  }
  /* Back of card */
  .card-back { top: 40px; }
  .card-back__pattern {
    position: absolute; inset: 0;
    background: radial-gradient(ellipse at 50% 45%, var(--navy-soft) 0%, var(--navy) 55%, var(--navy-deep) 100%);
  }
  .card-back__brand {
    position: absolute; left: 50%; top: 50%; transform: translate(-50%, -50%);
    display: flex; align-items: center; gap: 12px;
  }
  .card-back__dot {
    width: 14px; height: 14px; border: 2px solid var(--paper); border-radius: 50%;
  }
  .card-back__name {
    color: var(--paper); font-weight: 700; font-size: 18px;
    letter-spacing: 3px; text-transform: uppercase;
  }
  /* Front of card */
  .card-front { top: 470px; background: var(--paper); }
  .card-front__ring {
    position: absolute; left: 0; top: 0;
  }
  .card-front__brand {
    position: absolute; left: 48px; top: 52px;
    color: var(--ink); font-weight: 700; font-size: 34px;
    letter-spacing: 3px; text-transform: uppercase;
  }
  .holder { position: absolute; left: 48px; top: 150px; color: var(--ink); }
  .holder__name { font-weight: 700; font-size: 27px; }
  .holder__role { font-size: 19px; color: var(--muted); margin-top: 2px; }
  .contact { position: absolute; left: 48px; top: 240px; list-style: none; color: var(--ink); }
  .contact__item {
    display: flex; align-items: center; gap: 10px;
    font-size: 18px; line-height: 28px;
  }
  .contact__icon { width: 18px; height: 18px; flex: none; }
  .address {
    position: absolute; left: 48px; top: 330px;
    font-size: 18px; line-height: 24px; color: var(--ink);
  }
</style>
</head>
<body>
<main class="stage">
  <section class="card card-back" aria-label="Card back">
    <div class="card-back__pattern" role="img" aria-label="Dark navy surface with a blind-embossed repeating monogram pattern"></div>
    <div class="card-back__brand">
      <span class="card-back__dot"></span>
      <span class="card-back__name">Corvane Capital</span>
    </div>
  </section>

  <section class="card card-front" aria-label="Card front">
    <svg class="card-front__ring" width="700" height="400" viewBox="0 0 700 400" aria-hidden="true">
      <circle cx="555" cy="150" r="125" fill="none" stroke="var(--ink)" stroke-width="6"/>
    </svg>
    <div class="card-front__brand">Corvane Capital</div>

    <div class="holder">
      <div class="holder__name">Daniel Hartley</div>
      <div class="holder__role">Owner</div>
    </div>

    <ul class="contact">
      <li class="contact__item">
        <svg class="contact__icon" viewBox="0 0 24 24" aria-hidden="true"><path fill="var(--ink)" d="M6.6 10.8a15 15 0 0 0 6.6 6.6l2.2-2.2a1 1 0 0 1 1-.25 11.4 11.4 0 0 0 3.6.57 1 1 0 0 1 1 1V20a1 1 0 0 1-1 1A17 17 0 0 1 3 4a1 1 0 0 1 1-1h3.5a1 1 0 0 1 1 1c0 1.25.2 2.45.57 3.57a1 1 0 0 1-.25 1z"/></svg>
        044-555 018 342
      </li>
      <li class="contact__item">
        <svg class="contact__icon" viewBox="0 0 24 24" aria-hidden="true"><path fill="var(--ink)" d="M2 5h20v14H2zm2 2v.5l8 5 8-5V7l-8 5z"/></svg>
        info@corvanecapital.com
      </li>
      <li class="contact__item">
        <svg class="contact__icon" viewBox="0 0 24 24" aria-hidden="true"><circle cx="12" cy="12" r="10" fill="none" stroke="var(--ink)" stroke-width="2"/><path d="M2 12h20M12 2c3 3 3 17 0 20M12 2c-3 3-3 17 0 20" fill="none" stroke="var(--ink)" stroke-width="1.6"/></svg>
        www.corvanecapital.com
      </li>
    </ul>

    <address class="address" style="font-style:normal">
      421, Address line goes here<br>
      45452, Country name
    </address>
  </section>
</main>
</body>
</html>
```